Business cards for Zestcycle

We need a business card layout for our new bike and e-bike rental (we also sell used e-bikes and bike accessories). The logo already exists.

```html
<!DOCTYPE html>
<html lang="en">
<head>
<meta charset="utf-8">
<title>Zestcycle – Business Cards</title>
<link rel="stylesheet" href="https://fonts.googleapis.com/css2?family=Open+Sans:wght@400;500;600;700&family=Arimo:wght@400;700&display=swap">
<style>
  :root {
    --backdrop: #ece7e0;
    --kraft-light: #d9b383;
    --kraft-mid: #c99c67;
    --kraft-dark: #b8874f;
    --ink: #1c140c;
    --card-shadow: rgba(40, 22, 8, 0.35);
  }
  * { margin: 0; padding: 0; box-sizing: border-box; }
  html, body {
    width: 1200px;
    height: 900px;
    overflow: hidden;
    background: var(--backdrop);
  }
  .canvas {
    position: relative;
    width: 1200px;
    height: 900px;
  }
  .card {
    position: absolute;
    width: 556px;
    height: 343px;
    background: linear-gradient(135deg, var(--kraft-light) 0%, var(--kraft-mid) 45%, var(--kraft-dark) 100%);
    box-shadow: 2px 3px 6px var(--card-shadow);
    color: var(--ink);
    text-align: center;
  }
  .card--contact { left: 330px; top: 90px; }
  .card--brand { left: 330px; top: 470px; width: 558px; }

  /* Contact side */
  .person-name {
    position: absolute;
    top: 62px; left: 0; right: 0;
    font-family: "Open Sans", Arial, sans-serif;
    font-weight: 700;
    font-size: 20px;
    letter-spacing: 0.3px;
  }
  .person-role {
    position: absolute;
    top: 86px; left: 0; right: 0;
    font-family: "Arimo", Arial, sans-serif;
    font-size: 16px;
  }
  .rule {
    position: absolute;
    height: 1px;
    background: var(--ink);
  }
  .card--contact .rule { left: 180px; width: 195px; }
  .rule--upper { top: 116px; }
  .rule--lower { top: 221px; }
  .contact-list {
    position: absolute;
    top: 129px; left: 0; right: 0;
    list-style: none;
    font-family: "Arimo", Arial, sans-serif;
    font-size: 16px;
    line-height: 20px;
  }
  .contact-list b { font-weight: 700; }
  .address {
    position: absolute;
    top: 239px; left: 0; right: 0;
    font-family: "Arimo", Arial, sans-serif;
    font-size: 16px;
    line-height: 20px;
    font-style: normal;
  }

  /* Brand side */
  .brand-dot {
    position: absolute;
    top: 62px;
    left: 261px;
    width: 36px;
    height: 36px;
    border-radius: 50%;
    background: var(--ink);
  }
  .brand-name {
    position: absolute;
    top: 120px; left: 0; right: 0;
    font-family: "Open Sans", Arial, sans-serif;
    font-weight: 400;
    font-size: 62px;
    line-height: 80px;
    letter-spacing: 1px;
  }
  .tagline {
    position: absolute;
    top: 216px; left: 0; right: 0;
    font-family: "Open Sans", Arial, sans-serif;
    font-weight: 600;
    font-size: 16px;
  }
  .card--brand .rule { top: 263px; left: 131px; width: 296px; }
  .services {
    position: absolute;
    top: 278px; left: 0; right: 0;
    list-style: none;
    font-family: "Open Sans", Arial, sans-serif;
    font-weight: 600;
    font-size: 14px;
    line-height: 17px;
    letter-spacing: 0.2px;
    text-transform: uppercase;
  }
</style>
</head>
<body>
<main class="canvas">
  <section class="card card--contact" aria-label="Contact side">
    <h1 class="person-name">DANIEL HARPER</h1>
    <p class="person-role">Managing Director</p>
    <div class="rule rule--upper"></div>
    <ul class="contact-list">
      <li><b>P:</b> 044-123 456 789</li>
      <li><b>M:</b> 044-123 456 789</li>
      <li><b>E:</b> info@webname.com</li>
      <li><b>W:</b> www.websitename.com</li>
    </ul>
    <div class="rule rule--lower"></div>
    <address class="address">12345, Address Goes Here<br>Country Name, 123456.</address>
  </section>

  <section class="card card--brand" aria-label="Brand side">
    <span class="brand-dot"></span>
    <h2 class="brand-name">ZESTCYCLE</h2>
    <p class="tagline">e-leicht unterwegs</p>
    <div class="rule"></div>
    <ul class="services">
      <li>New bike and e-bike rental</li>
      <li>Sell used e-bikes and bike accessories</li>
    </ul>
  </section>
</main>
</body>
</html>
```